Healthcare and Professional IT Services Company need a redesigned business card

We are a IT Services company that targets small medical practices and professional business such as Attorneys, Accounts, Architects etc. We want to communicate a professional yet friendly image using recent logo redesign here on ArtHarbor. Like to see the colors blue and orange in the design. Must use the Tall Pine Computing as displayed in the new logo - then also want to incorporate the fish logo as well.

Target Market(s)

Small medical and professional services

Industry/Entity Type

It Company

Contact Information for Business Card

The usual stuff, place for name address phone website. Also maybe our tagline which is "rooted in technology"

Requirements
Must have
• My new logo and the fish somewhere on the card

```html
<!DOCTYPE html>
<html lang="en">
<head>
<meta charset="utf-8">
<title>Tall Pine Computing – Business Card</title>
<link href="https://fonts.googleapis.com/css2?family=Open+Sans:wght@400;600;700&display=swap" rel="stylesheet">
<style>
  :root {
    --bg: #e4e6e9;
    --blue: #1e95d3;
    --blue-deep: #0f78b4;
    --orange: #f29a2e;
    --ink: #3a3a3a;
    --white: #ffffff;
  }
  * { box-sizing: border-box; margin: 0; padding: 0; }
  html, body { width: 1200px; height: 871px; overflow: hidden; }
  body {
    background: var(--bg);
    font-family: "Open Sans", Arial, sans-serif;
    display: flex;
    align-items: center;
    justify-content: center;
    gap: 40px;
  }
  .card {
    width: 540px;
    height: 309px;
    position: relative;
    overflow: hidden;
    box-shadow: 0 6px 18px rgba(0,0,0,0.18);
  }

  /* Back side */
  .card-back {
    background: linear-gradient(135deg, #2aa4e0 0%, var(--blue) 45%, var(--blue-deep) 100%);
    color: var(--white);
  }
  .card-back .brand-name {
    position: absolute;
    left: 0; right: 0; top: 112px;
    font-size: 34px;
    font-weight: 700;
    letter-spacing: 0.5px;
    display: flex;
    align-items: center;
    justify-content: center;
    gap: 12px;
  }
  .brand-mark { width: 18px; height: 18px; border-radius: 50%; background: currentColor; display: inline-block; flex: none; }
  .card-back .tagline {
    position: absolute;
    left: 0; right: 0; top: 232px;
    text-align: center;
    font-size: 16px;
    font-weight: 600;
    opacity: 0.9;
  }

  /* Front side */
  .card-front { background: linear-gradient(180deg, var(--white) 70%, #f0f1f2 100%); }
  .front-main { position: absolute; left: 38px; top: 40px; }
  .front-main .brand-name {
    font-size: 30px;
    font-weight: 700;
    color: var(--blue);
    line-height: 1.1;
    display: flex;
    align-items: center;
    gap: 10px;
    margin-bottom: 34px;
  }
  .address { font-size: 14px; color: var(--ink); line-height: 1.45; margin-bottom: 8px; }
  .contact-list { list-style: none; font-size: 14px; color: var(--ink); }
  .contact-list li { display: flex; align-items: center; gap: 10px; line-height: 1.7; }
  .contact-list svg { width: 14px; height: 14px; fill: var(--blue); flex: none; }

  .name-band {
    position: absolute;
    right: 0; top: 0; bottom: 0;
    width: 96px;
    background: linear-gradient(180deg, #2aa4e0, var(--blue-deep));
    border-left: 3px solid var(--orange);
    box-shadow: inset 3px 0 0 var(--white);
  }
  .name-band .person {
    position: absolute;
    left: 50%; top: 50%;
    transform: translate(-50%, -50%) rotate(-90deg);
    white-space: nowrap;
    color: var(--white);
    text-align: left;
  }
  .person .person-name { font-size: 20px; font-weight: 600; display: block; }
  .person .person-title { font-size: 13px; opacity: 0.9; display: block; }
</style>
</head>
<body>
  <section class="card card-back" aria-label="Business card back">
    <div class="brand-name"><span class="brand-mark"></span>Tall Pine Computing</div>
    <div class="tagline">rooted in technology</div>
  </section>

  <section class="card card-front" aria-label="Business card front">
    <div class="front-main">
      <div class="brand-name"><span class="brand-mark"></span>Tall Pine<br>Computing</div>
      <p class="address">4127 Harbor Ridge Lane<br>Cedar Point, NY 11240</p>
      <ul class="contact-list">
        <li>
          <svg viewBox="0 0 16 16" aria-hidden="true"><path d="M3 1l3 3-2 2c1 2 3 4 5 5l2-2 3 3-2 3C6 15 1 10 1 3z"/></svg>
          555 0142 7789
        </li>
        <li>
          <svg viewBox="0 0 16 16" aria-hidden="true"><path d="M1 3h14v10H1z M1 3l7 6 7-6" fill="none" stroke="#1e95d3" stroke-width="1.6"/></svg>
          evan@tallpine.example
        </li>
        <li>
          <svg viewBox="0 0 16 16" aria-hidden="true"><circle cx="8" cy="8" r="7"/><path d="M1 8h14M8 1c3 3 3 11 0 14M8 1c-3 3-3 11 0 14" stroke="#fff" stroke-width="1" fill="none"/></svg>
          www.tallpine.example
        </li>
      </ul>
    </div>
    <div class="name-band">
      <div class="person">
        <span class="person-name">Evan Marlowe</span>
        <span class="person-title">President</span>
      </div>
    </div>
  </section>
</body>
</html>
```